Kickbut Home Page Design built to Sell

We need a new home page layout. The website is working now but we need a refresh. Our business has slowed down since a few years ago. We need to show we build ecommerce and membership websites. Here is the page now: https://www.brelvoxstudio.graphics/new-home/

Target Market(s)

Women, solopreneurs, artists, politicians

Industry/Entity Type

Design Agency

Number of Pages Required

1 page

Font styles to use
Sans Serif

Colors
b8a6cd
fabb94
acd136
00a990

Requirements
Must have
• Video header
Section for text and Step process similar to this website: https://quintarelweb.com/ [This is out sister company]
Places for images.
Call to action lead gen form and Get a quote.
The menu should show WEB, PRINT, VIDEO
Nice to have
• I LOVE this company: https://tarnwickly.com/guide/
Area for testimonials
Should not have
• We don't want a duplicate of https://quintarelweb.com/

```html
<!DOCTYPE html>
<html lang="en">
<head>
<meta charset="utf-8">
<title>Brelvoxstudio — Lead Generating Websites</title>
<link href="https://fonts.googleapis.com/css2?family=Oswald:wght@400;500&family=Bebas+Neue&display=swap" rel="stylesheet">
<style>
:root{
  --lime:#9bc92a;
  --lime-btn:#8cc63f;
  --teal:#1a9c7c;
  --teal-dark:#0e8a74;
  --ink:#3a3a3a;
  --body:#6b6b6b;
  --footer:#2b2b2b;
  --white:#ffffff;
}
*{box-sizing:border-box;margin:0;padding:0}
html,body{width:1200px;height:3494px;overflow:hidden}
body{position:relative;background:var(--white);font-family:Arial,Helvetica,sans-serif;color:var(--body)}
.abs{position:absolute}
.display{font-family:'Bebas Neue','Oswald',sans-serif;font-weight:400;letter-spacing:.5px}
.cond{font-family:'Oswald',sans-serif;font-weight:500}

/* hero */
.hero{left:0;top:0;width:1200px;height:782px;background:linear-gradient(135deg,#3b3530 0%,#2a2622 40%,#4a3c30 70%,#2c2824 100%)}
.hero-shade{left:0;top:0;width:1200px;height:782px;background:rgba(0,0,0,.35)}
.brand{color:var(--white)}
.brand-name{font-family:'Oswald',sans-serif;font-weight:500;font-size:50px;line-height:1;letter-spacing:1px}
.brand-tag{font-size:12.5px;letter-spacing:2.6px;margin-top:6px}
.nav a{position:absolute;top:66px;color:var(--white);text-decoration:none;font-family:'Oswald',sans-serif;font-weight:500;font-size:16px;transform:scaleX(.85);transform-origin:left}
.member{left:930px;top:50px;width:159px;height:51px;border-radius:26px;background:var(--lime-btn);color:var(--white);text-align:center;line-height:51px;font-family:'Oswald',sans-serif;font-weight:500;font-size:17px}
.hero-title{left:0;width:1200px;top:345px;text-align:center;color:var(--white);font-size:104px;line-height:1}
.hero-sub{left:0;width:1200px;top:470px;text-align:center;color:var(--white);font-size:36px;line-height:1}

/* headings */
.h2{color:var(--ink);font-size:42px;line-height:1}
.rule{height:3px;width:48px;background:var(--teal)}
.rule-w{background:var(--white)}

/* process */
.process-img{left:0;top:782px;width:599px;height:476px;background:linear-gradient(120deg,#d9d3cb 0%,#bfb4a6 45%,#8d7260 75%,#6b5244 100%)}
.step-icon{width:88px;height:88px;border-radius:50%;background:linear-gradient(135deg,var(--teal) 20%,var(--lime) 100%)}
.step-title{color:var(--ink);font-size:21px;line-height:1}
.step-text{font-size:14px;line-height:22px;color:var(--body);width:330px}

/* portfolio */
.tile{width:321px;height:288px}
.t1{background:linear-gradient(135deg,#4a4340,#8c6e62 60%,#b0433e)}
.t2{background:linear-gradient(135deg,#2f9a6b,#5fb56a 60%,#7dc46c)}
.t3{background:linear-gradient(135deg,#c9c4be,#9a8b7f 60%,#6d7f8a)}
.t4{background:linear-gradient(135deg,#574b44,#8a7568 60%,#b9a898)}
.t5{background:linear-gradient(135deg,#d8d4cf,#9d958e 60%,#4c4a4c)}
.t6{background:linear-gradient(135deg,#7e4b3c,#a4725c 50%,#d9c9b8)}

/* quote */
.quote-panel{left:0;top:2091px;width:614px;height:494px;background:var(--lime)}
.quote-img{left:614px;top:2091px;width:586px;height:494px;background:linear-gradient(120deg,#eeece8 0%,#d6d1c8 50%,#5f6f84 80%,#3e4a5a 100%)}
.field{left:112px;width:410px;background:var(--white);border:1px solid #e2e2e2;font-size:14px;color:#444;padding-left:21px}
.btn{left:112px;top:2495px;width:410px;height:45px;background:var(--teal-dark);color:var(--white);text-align:center;line-height:45px;font-size:24px}

/* testimonial */
.portrait{left:175px;top:2759px;width:330px;height:330px;border-radius:50%;border-bottom:5px solid var(--teal);background:linear-gradient(160deg,#e9eef1 0%,#cfd9e0 50%,#9fb1c0 100%)}
.quote-text{left:553px;top:2806px;width:510px;font-size:14px;line-height:27.5px;color:#666}
.client{left:553px;top:2990px;color:var(--teal);font-size:20px}
.client-role{left:553px;top:3023px;font-size:14px;color:#666}

/* footer */
.footer{left:0;top:3150px;width:1200px;height:344px;background:var(--footer)}
.f-text{color:#e8e8e8;font-size:15px;line-height:23px}
.vline{width:1px;height:160px;background:#4a4a4a}
.social{width:42px;height:42px;border-radius:50%;border:2px solid #e8e8e8}
.f-nav a{position:absolute;top:3437px;color:#f0f0f0;text-decoration:none;font-size:16px;font-weight:bold}
</style>
</head>
<body>

<!-- Hero -->
<div class="abs hero" role="img" aria-label="Background video: developers collaborating at computer screens in a studio"></div>
<div class="abs hero-shade"></div>
<div class="abs brand" style="left:111px;top:40px">
  <div class="brand-name">BRELVOXSTUDIO</div>
  <div class="brand-tag">GRAPHICS WEB VIDEO CONSULTANTS</div>
</div>
<nav class="nav">
  <a href="#" style="left:612px">HOME</a>
  <a href="#" style="left:691px">WEB</a>
  <a href="#" style="left:774px">PRINT</a>
  <a href="#" style="left:866px">VIDEO</a>
</nav>
<div class="abs member">MEMBERSHIP</div>
<h1 class="abs display hero-title">BRELVOXSTUDIO</h1>
<div class="abs display hero-sub">LEAD GENERATING WEBSITES THAT MOVE YOUR BUSINESS FORWARD</div>
<svg class="abs" style="left:551px;top:533px" width="98" height="98" viewBox="0 0 98 98" aria-label="Play video">
  <circle cx="49" cy="49" r="46" fill="none" stroke="#fff" stroke-width="3"/>
  <path d="M39 32 L66 49 L39 66 Z" fill="#fff"/>
</svg>

<!-- Process -->
<div class="abs process-img" role="img" aria-label="Photo: woman at a desktop showing website wireframes"></div>
<h2 class="abs display h2" style="left:642px;top:822px">OUR PROCESS</h2>
<div class="abs rule" style="left:642px;top:872px"></div>

<div class="abs step-icon" style="left:641px;top:904px"></div>
<svg class="abs" style="left:641px;top:904px" width="88" height="88" viewBox="0 0 88 88">
  <ellipse cx="44" cy="42" rx="22" ry="17" fill="none" stroke="#fff" stroke-width="2.5"/>
  <path d="M30 54 L26 64 L38 58" fill="none" stroke="#fff" stroke-width="2.5" stroke-linejoin="round"/>
  <path d="M34 37h20M34 43h20M38 49h12" stroke="#fff" stroke-width="2.5"/>
</svg>
<div class="abs display step-title" style="left:755px;top:912px">STEP 1 - TELL US YOUR NEEDS</div>
<p class="abs step-text" style="left:756px;top:944px">Sed ut perspiciatis unde omnis iste natus error sit voluptatem accusantium</p>

<div class="abs step-icon" style="left:641px;top:1026px"></div>
<svg class="abs" style="left:641px;top:1026px" width="88" height="88" viewBox="0 0 88 88">
  <path d="M30 28c3-2 6-1 7 2l3 7c1 2 0 4-2 5l-3 2c2 5 6 9 11 11l2-3c1-2 3-3 5-2l7 3c3 1 4 4 2 7l-3 3c-4 4-16 0-25-9s-13-21-9-25z" fill="none" stroke="#fff" stroke-width="2.5"/>
  <path d="M48 28a12 12 0 0 1 12 12M48 20a20 20 0 0 1 20 20" fill="none" stroke="#fff" stroke-width="2.5"/>
</svg>
<div class="abs display step-title" style="left:755px;top:1034px">STEP 2 - PHONE CALL</div>
<p class="abs step-text" style="left:756px;top:1066px">Sed ut perspiciatis unde omnis iste natus error sit voluptatem accusantium</p>

<div class="abs step-icon" style="left:641px;top:1148px"></div>
<svg class="abs" style="left:641px;top:1148px" width="88" height="88" viewBox="0 0 88 88">
  <path d="M40 30c-10 2-16 10-16 20a7 7 0 1 0 7-7M62 30c-10 2-16 10-16 20a7 7 0 1 0 7-7" fill="none" stroke="#fff" stroke-width="3" stroke-linecap="round"/>
</svg>
<div class="abs display step-title" style="left:755px;top:1156px">STEP 3 - CUSTOM QUOTE ARRIVES</div>
<p class="abs step-text" style="left:756px;top:1188px">Sed ut perspiciatis unde omnis iste natus error sit voluptatem accusantium</p>

<!-- Portfolio -->
<h2 class="abs display h2" style="left:0;width:1200px;text-align:center;top:1327px">PORTFOLIO OF WORK</h2>
<div class="abs rule" style="left:576px;top:1377px"></div>
<div class="abs tile t1" style="left:111px;top:1413px" role="img" aria-label="Project photo: team reviewing code on monitors"></div>
<div class="abs tile t2" style="left:439px;top:1413px" role="img" aria-label="Project photo: designer sketching, highlighted"></div>
<svg class="abs" style="left:563px;top:1521px" width="72" height="72" viewBox="0 0 72 72" aria-label="Open project">
  <circle cx="36" cy="36" r="33" fill="none" stroke="#fff" stroke-width="3"/>
  <path d="M36 18v36M18 36h36" stroke="#fff" stroke-width="6"/>
</svg>
<div class="abs tile t3" style="left:767px;top:1413px" role="img" aria-label="Project photo: colleagues discussing at a laptop"></div>
<div class="abs tile t4" style="left:111px;top:1709px" role="img" aria-label="Project photo: developers pointing at a screen"></div>
<div class="abs tile t5" style="left:439px;top:1709px" role="img" aria-label="Project photo: programmer working on laptop"></div>
<div class="abs tile t6" style="left:767px;top:1709px" role="img" aria-label="Project photo: colour swatches and sketches on a desk"></div>

<!-- Quote -->
<div class="abs quote-panel"></div>
<div class="abs quote-img" role="img" aria-label="Photo: woman working at a desktop computer"></div>
<h2 class="abs display" style="left:111px;top:2126px;color:#fff;font-size:42px;line-height:1">REQUEST A QUOTE</h2>
<div class="abs rule rule-w" style="left:112px;top:2178px"></div>
<div class="abs field" style="top:2198px;height:45px;line-height:45px">Name :</div>
<div class="abs field" style="top:2253px;height:45px;line-height:45px">Email :</div>
<div class="abs field" style="top:2307px;height:45px;line-height:45px">Phone :</div>
<div class="abs field" style="top:2362px;height:121px;padding-top:15px">Message :</div>
<div class="abs display btn">GET A QUOTE</div>

<!-- Testimonials -->
<h2 class="abs display h2" style="left:0;width:1200px;text-align:center;top:2645px">WHY OUR CLIENTS LOVE US</h2>
<div class="abs rule" style="left:576px;top:2695px"></div>
<div class="abs portrait" role="img" aria-label="Client portrait"></div>
<p class="abs quote-text">Dana Whitlock was great to work with and extremely knowledgeable and accessible. I especially appreciated his well thought out design process and the client videos he created to walk me through various stages of it. I received lots of great feedback on the visual look, user-friendliness, and rich content of my website throughout the campaign and was re-elected overwhelmingly. I highly recommend Dana and Quintarel Web for your next project!</p>
<div class="abs display client">MARCUS DELANO</div>
<div class="abs client-role">Mayor, Riverton, Ma</div>

<!-- Footer -->
<div class="abs footer"></div>
<div class="abs brand" style="left:126px;top:3238px">
  <div class="brand-name" style="font-size:48px">BRELVOXSTUDIO</div>
  <div class="brand-tag" style="font-size:12px">GRAPHICS WEB VIDEO CONSULTANTS</div>
</div>
<div class="abs vline" style="left:445px;top:3210px"></div>
<svg class="abs" style="left:490px;top:3226px" width="22" height="26" viewBox="0 0 22 26">
  <path d="M11 24c-5-6-8-10-8-14a8 8 0 0 1 16 0c0 4-3 8-8 14z" fill="none" stroke="#ddd" stroke-width="1.6"/>
  <circle cx="11" cy="10" r="3" fill="none" stroke="#ddd" stroke-width="1.6"/>
</svg>
<div class="abs f-text" style="left:530px;top:3217px">Address<br>17 Alder Row, Fenwick<br>MA 01099</div>
<div class="abs social" style="left:530px;top:3300px"></div>
<div class="abs social" style="left:582px;top:3300px"></div>
<div class="abs vline" style="left:776px;top:3210px"></div>
<svg class="abs" style="left:828px;top:3230px" width="22" height="22" viewBox="0 0 22 22">
  <path d="M4 2c2-1 3 0 4 2l1 3c0 1 0 2-1 2l-1 1c1 3 3 5 6 6l1-1c1-1 2-1 3 0l3 1c2 1 2 2 1 4l-2 1c-3 2-8-1-11-4S2 5 4 2z" fill="none" stroke="#ddd" stroke-width="1.5"/>
</svg>
<div class="abs f-text" style="left:868px;top:3217px">Phone:<br>1-555-014-2287</div>
<svg class="abs" style="left:830px;top:3296px" width="22" height="16" viewBox="0 0 22 16">
  <rect x="1" y="1" width="20" height="14" fill="none" stroke="#ddd" stroke-width="1.5"/>
  <path d="M1 1l10 8 10-8" fill="none" stroke="#ddd" stroke-width="1.5"/>
</svg>
<div class="abs f-text" style="left:870px;top:3287px">Email:<br>dana@quintarelweb.com</div>
<div class="abs" style="left:111px;top:3397px;width:978px;height:1px;background:#444"></div>
<nav class="f-nav">
  <a href="#" style="left:111px">HOME</a>
  <a href="#" style="left:217px">WEB</a>
  <a href="#" style="left:311px">PRINT</a>
  <a href="#" style="left:416px">VIDEO</a>
</nav>
<div class="abs f-text" style="left:700px;width:390px;text-align:right;top:3435px">brelvoxstudio © 2021.All Rights Reserved</div>

</body>
</html>
```